BildeVOLD buisnesscard

Hey :) I need a modern buisnesscard for my company BildeVOLD
It most have:
Dagligleder og Fotograf: Henrik Audun Strandvik

Mob: +4791264085
Epost: post@bildevold.example
Adresse: Kvernbakken9, 6040 Fjordvik

Facbook and instagram logo with text BildeVOLD

BildeVOLD logo

It Company

```html
<!DOCTYPE html>
<html lang="no">
<head>
<meta charset="utf-8">
<title>BildeVOLD – visittkort</title>
<link rel="stylesheet" href="https://fonts.googleapis.com/css2?family=Kanit:wght@300;400;600&display=swap">
<style>
  :root {
    --page-bg: #e9e9ea;
    --card-white: #ffffff;
    --grey-light: #dcdcde;
    --grey-mid: #bdbdc0;
    --grey-dark: #a9a9ac;
    --brand-grey: #9c9c9f;
    --text-dark: #3f3f42;
    --text-mid: #5a5a5d;
  }
  * { box-sizing: border-box; margin: 0; padding: 0; }
  html, body {
    width: 1200px;
    height: 1050px;
    overflow: hidden;
    background: var(--page-bg);
    font-family: "Kanit", sans-serif;
  }
  .sheet {
    width: 1200px;
    height: 1050px;
    display: flex;
    flex-direction: column;
    align-items: center;
    justify-content: center;
    gap: 50px;
  }
  .card {
    position: relative;
    width: 760px;
    height: 440px;
    background: var(--card-white);
    box-shadow: 0 6px 20px rgba(0,0,0,0.12);
    overflow: hidden;
  }
  .card-shapes {
    position: absolute;
    inset: 0;
    width: 100%;
    height: 100%;
  }
  .brand-name {
    font-family: "Kanit", sans-serif;
    font-weight: 600;
    color: var(--brand-grey);
    letter-spacing: 0.5px;
    line-height: 1;
    white-space: nowrap;
  }

  /* Back side */
  .card-back .brand-name {
    position: absolute;
    left: 0; right: 0;
    top: 160px;
    text-align: center;
    font-size: 76px;
  }
  .social-row {
    position: absolute;
    left: 150px; right: 150px;
    top: 270px;
    display: flex;
    justify-content: space-between;
  }
  .social-handle {
    display: flex;
    align-items: center;
    gap: 8px;
    font-size: 21px;
    font-weight: 400;
    color: var(--brand-grey);
  }
  .social-handle .marker {
    width: 18px;
    height: 18px;
    background: var(--brand-grey);
    border-radius: 3px;
  }

  /* Front side */
  .card-front .brand-name {
    position: absolute;
    left: 40px;
    top: 112px;
    font-size: 58px;
  }
  .role-block {
    position: absolute;
    left: 410px;
    top: 80px;
    color: var(--text-mid);
    white-space: nowrap;
  }
  .role-title {
    font-size: 20px;
    font-weight: 300;
  }
  .role-name {
    margin-top: 2px;
    font-size: 18px;
    font-weight: 300;
    text-transform: uppercase;
    letter-spacing: 0.3px;
  }
  .contact {
    position: absolute;
    left: 60px;
    top: 320px;
    color: var(--text-dark);
    font-size: 18px;
    font-weight: 300;
    line-height: 1.65;
    white-space: nowrap;
  }
</style>
</head>
<body>
<main class="sheet">

  <section class="card card-back" aria-label="Baksiden av visittkortet">
    <svg class="card-shapes" viewBox="0 0 760 440" preserveAspectRatio="none" aria-hidden="true">
      <polygon points="0,0 760,0 760,55 420,70 0,40" fill="var(--grey-light)"/>
      <polygon points="0,0 330,0 90,120 0,140" fill="var(--grey-mid)"/>
      <polygon points="330,0 760,0 760,30 560,50" fill="var(--grey-mid)"/>
      <polygon points="0,250 240,440 0,440" fill="var(--grey-light)"/>
      <polygon points="0,310 170,440 0,440" fill="var(--grey-dark)"/>
      <polygon points="760,210 610,440 760,440" fill="var(--grey-light)"/>
      <polygon points="760,300 690,440 760,440" fill="var(--grey-mid)"/>
    </svg>
    <div class="brand-name">BildeVOLD</div>
    <div class="social-row">
      <span class="social-handle"><span class="marker"></span>/BildeVOLD</span>
      <span class="social-handle"><span class="marker"></span>/BildeVOLD</span>
    </div>
  </section>

  <section class="card card-front" aria-label="Forsiden av visittkortet">
    <svg class="card-shapes" viewBox="0 0 760 440" preserveAspectRatio="none" aria-hidden="true">
      <polygon points="0,215 300,250 760,225 760,440 0,440" fill="var(--grey-light)"/>
      <polygon points="0,300 460,220 750,298 560,440 0,440" fill="var(--grey-mid)"/>
      <line x1="392" y1="150" x2="735" y2="158" stroke="var(--text-mid)" stroke-width="1.5"/>
      <polygon points="384,150 398,143 398,157" fill="var(--text-mid)"/>
    </svg>
    <div class="brand-name">BildeVOLD</div>
    <div class="role-block">
      <p class="role-title">Dagligleder og Fotograf:</p>
      <p class="role-name">Henrik Audun Strandvik</p>
    </div>
    <div class="contact">
      <p>Mob: +47 9126 4085 &nbsp;|&nbsp; Epost: post@bildevold.example</p>
      <p>Adresse: Kvernbakken9, 6040 Fjordvik</p>
    </div>
  </section>

</main>
</body>
</html>
```